Ledger Lanternfox Powerpoint with Marshal Valorline Type Theme

Need powerpoint template with matching colors and different slide options. Logo and colors to be used can be found at ledgerlanternfox.example. Want brightly colored slide deck that is readable form the back of a room, but highlights colors. I will be incorporating Quizzap into the slides to gamify my presentations.

Target Market(s)

Tech

Industry/Entity Type

IT, specifically database, but crossing over to mental health in IT, important note this is not for a company, this is just for a professional building a brand

Font styles to use
Sans Serif

Colors
0054AA
0677BA
7BADD7
CADEEF
E8F1F8
EB3D1F
EC4F4E
F09395
F8D3D4
FCEDEE

Requirements
Must have
• My Logo in the bottom corner, front page, a thank your page, question page, content page, content page with two columns, content page with graphs, and icons to be used in the primary colors of the logos, About Me Page, Break Slides, Demo break slide
Should not have
• Lighter shades of colors, I want to pop out where colors are used, I want spacing and font size to be readable from the back of a room, most likely black text and white background

```html
<!DOCTYPE html>
<html lang="en">
<head>
<meta charset="utf-8">
<title>Ledger Lanternfox – Slide Theme Overview</title>
<link href="https://fonts.googleapis.com/css2?family=Montserrat:wght@300;400;700&display=swap" rel="stylesheet">
<style>
:root{
  --navy:#0054AA; --blue:#0677BA; --sky:#12A6E8; --ice:#E8F1F8;
  --red:#EB3D1F; --coral:#EC4F4E; --ink:#1a1a1a; --grey:#8a8a8a; --text:#444; --page:#ffffff;
  --shadow:0 3px 9px rgba(0,0,0,.35);
}
*{box-sizing:border-box;margin:0;padding:0}
html,body{width:1143px;height:1200px;overflow:hidden;background:var(--page);font-family:"Montserrat",sans-serif;color:var(--ink)}
.deck{position:relative;width:1143px;height:1200px}
.slide{position:absolute;width:280px;height:157px;background:#fff;box-shadow:var(--shadow);overflow:hidden}
.c1{left:90px}.c2{left:431px}.c3{left:772px}
.r1{top:38px}.r2{top:232px}.r3{top:425px}.r4{top:618px}.r5{top:811px}.r6{top:1005px}
.foot-logo{position:absolute;left:19px;bottom:5px;font-size:3.6px;font-weight:700;color:var(--navy);display:flex;align-items:center;gap:2px}
.foot-logo::before{content:"";width:5px;height:5px;border-radius:50%;background:var(--red)}
.foot-url{position:absolute;right:22px;bottom:6px;font-size:3px;color:var(--grey)}
.foot-url.light{color:rgba(255,255,255,.55)}
.title{font-weight:300;font-size:13px;line-height:1.08;color:var(--ink)}
.title b{font-weight:700}
.title.center{position:absolute;left:0;right:0;text-align:center}
.sub{font-size:3.4px;color:var(--grey);margin-top:3px}
.body{font-size:3.2px;line-height:1.6;color:var(--text);text-align:justify}
.body p+p{margin-top:3px}
.vr{position:absolute;width:.5px;background:#bbb}
.fill{position:absolute}
.cover{background:linear-gradient(160deg,#1590d6 0%,var(--blue) 45%,var(--navy) 100%)}
.cover .art{position:absolute;left:95px;top:20px;width:90px;height:55px;border-radius:6px;background:rgba(0,60,130,.55);display:flex;align-items:center;justify-content:center}
.cover .art span{font-size:6px;font-weight:700;color:var(--red)}
.cover h1{position:absolute;left:0;right:0;top:104px;text-align:center;font-weight:300;color:#fff;font-size:11px;letter-spacing:.8px;line-height:1.3}
.agenda-head{position:absolute;left:24px;top:37px}
.agenda-head .a1{font-size:12px;color:var(--red)}
.agenda-head .a2{font-size:12px;color:var(--navy);font-weight:700;margin-top:-1px}
.agenda-list{position:absolute;left:134px;top:28px;list-style:none}
.agenda-list li{display:flex;gap:8px;height:13.3px}
.agenda-list .n{font-size:6.5px;color:var(--red);width:9px;padding-top:1px}
.agenda-list .t{font-size:4.8px;line-height:1.1}
.agenda-list .t small{display:block;font-size:3.2px;color:var(--grey)}
.photo{position:absolute;left:19px;top:31px;width:90px;height:96px;background:linear-gradient(135deg,#3a6ea5,#243a5e 60%,#4b2a3f)}
.photo::before{content:"";position:absolute;left:0;top:-2px;width:90px;height:2px;background:linear-gradient(90deg,var(--red) 40%,var(--navy) 40%)}
.about{position:absolute;left:117px;top:31px;width:146px}
.about h2{font-size:14px;font-weight:300}
.about h2 b{font-weight:700}
.about .name{font-size:6.5px;font-weight:300;margin-top:-1px}
.about .role{font-size:3px;color:#555;margin-bottom:3px}
.about .body{font-size:2.9px;line-height:1.45}
.mark{position:absolute;display:flex;align-items:center;justify-content:center;font-weight:700;color:var(--navy)}
.stat{height:23px;margin-bottom:3px;padding:3px 14px;color:#fff}
.stat b{font-size:5.5px;display:block}
.stat span{font-size:3px;line-height:1.4;display:block}
.navy{background:var(--navy)}.redbg{background:var(--red)}.skybg{background:var(--sky)}
.bar{height:15px;margin-bottom:4px;padding:3px 14px;color:#fff;font-size:3px;line-height:1.4}
ul.bul{list-style:none}
ul.bul li{position:relative;padding-left:5px}
ul.bul li+li{margin-top:2px}
ul.bul li::before{content:"•";position:absolute;left:0;color:var(--red)}
.band{display:flex;align-items:center;height:30px;margin-bottom:4px;color:#fff;padding-left:8px;gap:8px}
.band svg{width:16px;height:16px;flex:none}
.band b{font-size:4.6px;font-weight:400;display:block}
.band span{font-size:3px;display:block;line-height:1.35}
.feat{display:flex;gap:4px;width:76px}
.feat svg{width:10px;height:10px;flex:none}
.feat b{font-size:3.4px;display:block;line-height:1.3}
.feat span{font-size:2.8px;color:#666;display:block;line-height:1.5;margin-top:2px}
.num{color:var(--blue);font-weight:700;font-size:14px;text-align:center}
.num-cap{font-size:3.2px;font-weight:700;text-align:center;color:var(--navy);line-height:1.2}
.num-txt{font-size:2.8px;color:#666;text-align:center;line-height:1.5;margin-top:2px}
.icon-item{display:flex;gap:4px;align-items:flex-start}
.icon-item svg{width:10px;height:10px;flex:none}
.icon-item b{font-size:4px;font-weight:400;display:block;line-height:1.3}
.icon-item span{font-size:2.8px;color:#777;display:block;line-height:1.5;margin-top:2px}
.break{background:#1b2233}
.break h2{position:absolute;left:162px;top:44px;color:#fff;font-weight:300;font-size:17px;line-height:1.3;letter-spacing:.5px}
.qa{background:var(--sky)}
.qa h2{position:absolute;left:127px;top:44px;color:#fff;font-weight:300;font-size:38px;letter-spacing:1px}
.contact{background:linear-gradient(180deg,#f26a5e,var(--coral) 50%,#d83a2a)}
.contact h2{position:absolute;left:25px;top:40px;color:#fff;font-weight:300;font-size:14px;line-height:1.2}
.contact ul{position:absolute;left:27px;top:88px;list-style:none;color:#fff;font-size:3.6px}
.contact li{display:flex;align-items:center;gap:4px;height:11px}
.contact li svg{width:6px;height:6px}
.thanks{position:absolute;left:162px;top:60px;width:110px;text-align:center;color:#fff}
.thanks b{font-size:17px;font-weight:700;display:block}
.thanks span{font-size:6px;font-weight:300;display:block;margin-top:-3px}
</style>
</head>
<body>
<main class="deck">

<!-- Title slide -->
<section class="slide cover c1 r1">
  <div class="art" role="img" aria-label="Superhero hands opening a shirt to reveal the brand emblem"><span>Ledger Lanternfox</span></div>
  <h1>Your title Presentation Title<br>Template goes here</h1>
  <div class="foot-url light">ledgerlanternfox.example</div>
</section>

<section class="slide cover c2 r1">
  <div class="art" role="img" aria-label="Superhero hands opening a shirt to reveal the brand emblem"><span>Ledger Lanternfox</span></div>
  <h1>Your title Presentation Title<br>Template goes here</h1>
  <div class="foot-url light">ledgerlanternfox.example</div>
</section>

<!-- Agenda -->
<section class="slide c3 r1">
  <div class="agenda-head">
    <div class="a1">Agenda</div>
    <div class="a2">Presentation</div>
    <div class="sub">Table Of Contents</div>
  </div>
  <ul class="agenda-list">
    <li><span class="n">01</span><span class="t">Introduction<small>A short line about this part of the talk</small></span></li>
    <li><span class="n">02</span><span class="t">Topic #1<small>A short line about this part of the talk</small></span></li>
    <li><span class="n">03</span><span class="t">Topic #2<small>A short line about this part of the talk</small></span></li>
    <li><span class="n">04</span><span class="t">Topic #3<small>A short line about this part of the talk</small></span></li>
    <li><span class="n">05</span><span class="t">Topic #4<small>A short line about this part of the talk</small></span></li>
    <li><span class="n">06</span><span class="t">Topic #5<small>A short line about this part of the talk</small></span></li>
    <li><span class="n">07</span><span class="t">Appendix<small>A short line about this part of the talk</small></span></li>
  </ul>
  <div class="foot-logo">Ledger Lanternfox</div>
  <div class="foot-url">ledgerlanternfox.example &nbsp; 3</div>
</section>

<!-- About me -->
<section class="slide c1 r2">
  <div class="photo" role="img" aria-label="Portrait photo of the presenter in front of fireworks"></div>
  <div class="about">
    <h2>About <b>Me</b></h2>
    <div class="name">Wren Halvorsen</div>
    <div class="role">Data Platform Fellow, DataPath 2020 Award winner</div>
    <div class="body">
      <p>Works as a Senior Database Administrator for SignaDesk. Wren is a co-leader of the Piedmont Data User Group and the Query Circle Group, has spoken at many regional events, and has worked with databases since middle school, when a love of sports cards turned into a first tidy little table of records.</p>
      <p>When not busy in the data community Wren likes to make a difference as a Child Voice Advocate volunteer, speaking up for children in family court. This is a favorite and most rewarding role. Wren also serves on the Rights Council NC advisory board and talks openly about mental health in IT, drawing on lived experience to help others feel less alone and more supported at work.</p>
      <p>You may reach me by direct message on Chirpline.</p>
    </div>
  </div>
  <div class="foot-logo">Ledger Lanternfox</div>
  <div class="foot-url">ledgerlanternfox.example &nbsp; 4</div>
</section>

<!-- Title + emblem + text -->
<section class="slide c2 r2">
  <div style="position:absolute;left:12px;top:18px;text-align:center;width:98px">
    <div class="title" style="font-size:12px">Your title slide<br><b>will be here</b></div>
    <div class="sub">Your great Subtitle goes Here</div>
  </div>
  <div class="mark" style="left:24px;top:70px;width:74px;height:54px;font-size:6px;border:2px solid var(--navy);border-radius:50%">Ledger Lanternfox</div>
  <div class="vr" style="left:117px;top:18px;height:40px"></div>
  <div class="body" style="position:absolute;left:125px;top:18px;width:138px">
    <p>Sample copy sits here to show the body style of this deck and will be swapped for real content later. Keep each line short and clear so people at the back of the room can follow the idea. Use this opening block to frame the topic, name the problem and say why it matters to the people listening today.</p>
  </div>
  <ul class="body bul" style="position:absolute;left:125px;top:62px;width:138px">
    <li>Point one goes here with a short supporting sentence that explains the idea in plain words, so the whole room can follow it without squinting at the screen.</li>
    <li>Point two adds a detail or an example from real work with databases, showing how the idea plays out on an ordinary busy day.</li>
    <li>Point three wraps up the thought with a brief note, a simple takeaway or a lesson learned the hard way in production.</li>
    <li>Point four leads into the next slide with one last clear idea to remember, and a question for the audience to think about.</li>
  </ul>
  <div class="foot-logo">Ledger Lanternfox</div>
  <div class="foot-url">ledgerlanternfox.example &nbsp; 5</div>
</section>

<!-- Title + stats -->
<section class="slide c3 r2">
  <div style="position:absolute;left:19px;top:16px">
    <div class="title">Your title<br><b>slide here</b></div>
    <div class="sub">Great Subtitle Here</div>
  </div>
  <div class="vr" style="left:88px;top:16px;height:28px"></div>
  <div class="body" style="position:absolute;left:96px;top:16px;width:165px">Sample copy sits here to show the body style of this deck and will be swapped for real content later on. Keep each line short and clear so people at the back of the room can follow the main idea. This block sets up the three numbers shown below and explains where they come from.</div>
  <div class="body" style="position:absolute;left:19px;top:56px;width:104px">Sample copy sits here to show the body style and will be swapped for real content later. Keep lines short and clear so people at the back of the room can follow along. Use this column to explain the numbers on the right in a few calm and simple sentences, give a little context about how they were measured, and say what changed over time. A short closing line can point to the next step or a question to ask.</div>
  <div style="position:absolute;left:131px;top:58px;width:130px">
    <div class="stat navy"><b>1500+</b><span>Short note that explains this number for the audience in the room.</span></div>
    <div class="stat redbg"><b>900+</b><span>Short note that explains this number for the audience in the room.</span></div>
    <div class="stat skybg"><b>2900+</b><span>Short note that explains this number for the audience in the room.</span></div>
  </div>
  <div class="foot-logo">Ledger Lanternfox</div>
  <div class="foot-url">ledgerlanternfox.example &nbsp; 6</div>
</section>

<!-- Two column with boxes -->
<section class="slide c1 r3">
  <div style="position:absolute;left:22px;top:18px">
    <div class="title">Your title <b>slide</b></div>
    <div class="sub">Great Subtitle Here</div>
  </div>
  <div class="body" style="position:absolute;left:22px;top:42px;width:120px">Sample copy sits here to show the body style and will be swapped for real content later. Keep each line short and clear so people at the back of the room can follow the main idea. Use this column for the key message, then let the two colored notes below call out the most important points.</div>
  <div style="position:absolute;left:20px;top:104px;width:122px">
    <div class="bar navy">Short note that sits in the blue box for a key point.</div>
    <div class="bar redbg">Short note that sits in the red box for a warning.</div>
  </div>
  <div class="vr" style="left:152px;top:20px;height:30px"></div>
  <div class="body" style="position:absolute;left:160px;top:18px;width:104px">Sample copy sits here to show the body style and will be swapped for real content later. Keep each line short and clear so people at the back of the room can follow the main idea. Use this second column to add more detail, a short story or a worked example that supports the point on the left side of the slide. Talk through what was tried first, what went wrong and what finally worked. Close with one practical tip that people can take back to their own team and try the very next week.</div>
  <div class="foot-logo">Ledger Lanternfox</div>
  <div class="foot-url">ledgerlanternfox.example &nbsp; 7</div>
</section>

<!-- Break section -->
<section class="slide break c2 r3">
  <div class="fill" role="img" aria-label="Photo of a laptop keyboard with the brand emblem" style="inset:0;background:linear-gradient(160deg,#223049,#101521 70%)"></div>
  <div class="mark" style="left:20px;top:50px;width:90px;height:50px;font-size:6px;color:var(--red)">Ledger Lanternfox</div>
  <svg class="fill" style="inset:0" width="280" height="157" viewBox="0 0 280 157" aria-hidden="true"><path d="M135 0 H280 V157 H130 C108 110 108 45 135 0 Z" fill="#EB3D1F"/></svg>
  <h2>BREAK<br>SECTION<br>SLIDE</h2>
  <div class="foot-url light">ledgerlanternfox.example &nbsp; 8</div>
</section>

<!-- Full text extended -->
<section class="slide c3 r3">
  <div class="title center" style="top:18px;font-size:12.5px">Your Full Text <b>Title Slide Extended</b></div>
  <div class="body" style="position:absolute;left:20px;top:38px;width:242px">
    <p>Sample copy sits here to show the body style of this deck and will be swapped for real content later. Keep each line short and clear so people at the back of the room can follow the main idea being shared today. This opening paragraph sets the scene, names the problem and explains why it matters to the team, the business and the people who keep the data running every day.</p>
    <p>A second paragraph adds more detail. Use it to explain a process, give a short case or share a lesson learned from real work in the data field and beyond. Mention the tools involved, the time it took and the result that was reached in the end.</p>
  </div>
  <ul class="body bul" style="position:absolute;left:24px;top:98px;width:238px">
    <li>A first bullet with a longer line of supporting text that explains the idea to the audience in plain words, and gives one concrete example they will recognise from their own work.</li>
    <li style="margin-top:5px">A second bullet with another line of supporting text that adds one more useful detail to the topic, and points toward where people can learn more after the session ends.</li>
  </ul>
  <div class="foot-logo">Ledger Lanternfox</div>
  <div class="foot-url">ledgerlanternfox.example &nbsp; 9</div>
</section>

<!-- Full text two columns -->
<section class="slide c1 r4">
  <div class="title center" style="top:18px;font-size:12.5px">Your Full Text <b>Title Slide Extended</b></div>
  <div class="body" style="position:absolute;left:24px;top:38px;width:115px">Sample copy sits here to show the body style of this deck and will be swapped for real content later. Keep each line short and clear so people at the back of the room can follow the main idea. This first column can hold an overview, a short history or the reason the topic matters to the people in the room today, written in calm and simple words. Describe where things stood at the start, which signs showed that something needed to change, and who was affected along the way. Add a line about the data involved and how large it had grown over the years.</div>
  <div class="body" style="position:absolute;left:148px;top:38px;width:115px">A second column holds more detail. Use it to explain a process, give a short case study or share a lesson learned from real work. Keep the tone friendly and plain, and let each line lead to the next so the whole slide reads as one clear story. Walk through the steps that were taken, the checks that were added and the small wins that built trust with the team. Finish with what you would do differently next time, and one simple habit that anyone in the audience could start using on Monday morning.</div>
  <div class="foot-logo">Ledger Lanternfox</div>
  <div class="foot-url">ledgerlanternfox.example &nbsp; 10</div>
</section>

<!-- Title with three bands -->
<section class="slide c2 r4">
  <div class="title" style="position:absolute;left:19px;top:22px">Your title<br><b>slide will</b><br>be here</div>
  <div class="body" style="position:absolute;left:19px;top:76px;width:84px">Sample copy sits here to show the body style and will be swapped for real content later. Keep each line short and clear so people at the back of the room can follow the idea behind the three topics shown on the right side of this slide.</div>
  <div style="position:absolute;left:115px;top:22px;width:153px">
    <div class="band navy">
      <svg viewBox="0 0 24 24" fill="none" stroke="#fff" stroke-width="1.6"><path d="M7 17a4 4 0 0 1 0-8 5 5 0 0 1 9.6-1A4 4 0 0 1 17 17Z"/><path d="M8 21h8M12 17v4"/></svg>
      <div><b>Subtitle Here</b><span>Short line of sample copy for this row,<br>with a second line of detail.</span></div>
    </div>
    <div class="band redbg">
      <svg viewBox="0 0 24 24" fill="none" stroke="#fff" stroke-width="1.6"><path d="M7 16a4 4 0 0 1 0-8 5 5 0 0 1 9.6-1A4 4 0 0 1 17 16"/><path d="M12 11v9M9 17l3 3 3-3"/></svg>
      <div><b>Subtitle Here</b><span>Short line of sample copy for this row,<br>with a second line of detail.</span></div>
    </div>
    <div class="band skybg">
      <svg viewBox="0 0 24 24" fill="none" stroke="#fff" stroke-width="1.6"><ellipse cx="12" cy="5" rx="7" ry="2.5"/><path d="M5 5v14c0 1.4 3.1 2.5 7 2.5s7-1.1 7-2.5V5M5 10c0 1.4 3.1 2.5 7 2.5s7-1.1 7-2.5M5 15c0 1.4 3.1 2.5 7 2.5s7-1.1 7-2.5"/></svg>
      <div><b>Subtitle Here</b><span>Short line of sample copy for this row,<br>with a second line of detail.</span></div>
    </div>
  </div>
  <div class="foot-logo">Ledger Lanternfox</div>
  <div class="foot-url">ledgerlanternfox.example &nbsp; 11</div>
</section>

<!-- Title with icon features -->
<section class="slide c3 r4">
  <div style="position:absolute;left:19px;top:22px">
    <div class="title">Your title<br><b>slide will</b><br>be here</div>
    <div class="sub">Great Subtitle Here</div>
  </div>
  <div class="vr" style="left:90px;top:22px;height:30px"></div>
  <div class="body" style="position:absolute;left:98px;top:20px;width:165px">Sample copy sits here to show the body style of this deck and will be swapped for real content later. Keep each line short and clear so people at the back of the room can follow the main idea being shared on this slide. Use this block to introduce the three features below, explain how they fit together and why each one matters to the team that depends on the data every single day.</div>
  <div style="position:absolute;left:20px;top:90px;display:flex;gap:7px">
    <div class="feat">
      <svg viewBox="0 0 24 24" fill="none" stroke="#0054AA" stroke-width="2"><path d="M2 12s4-6 10-6 10 6 10 6-4 6-10 6S2 12 2 12Z"/><circle cx="12" cy="12" r="3"/></svg>
      <div><b>Short feature title for the first point</b><span>Sample copy sits here to show the body style and will be swapped for real content later on.</span></div>
    </div>
    <div class="feat">
      <svg viewBox="0 0 24 24" fill="none" stroke="#0054AA" stroke-width="2"><path d="M9 18h6M10 21h4M12 3a6 6 0 0 0-4 10.5c.7.7 1 1.5 1 2.5h6c0-1 .3-1.8 1-2.5A6 6 0 0 0 12 3Z"/></svg>
      <div><b>Short feature title for the next point</b><span>Sample copy sits here to show the body style and will be swapped for real content later on.</span></div>
    </div>
    <div class="feat">
      <svg viewBox="0 0 24 24" fill="none" stroke="#0054AA" stroke-width="2"><rect x="3" y="3" width="18" height="18"/><path d="M12 3v18M3 12h18M6 7.5h3M15 6l3 3M18 6l-3 3M6 16.5h3M15 16h3M15 18h3"/></svg>
      <div><b>Short feature title for the last point</b><span>Sample copy sits here to show the body style and will be swapped for real content later on.</span></div>
    </div>
  </div>
  <div class="foot-logo">Ledger Lanternfox</div>
  <div class="foot-url">ledgerlanternfox.example &nbsp; 12</div>
</section>

<!-- Text + 2x2 numbers -->
<section class="slide c1 r5">
  <div class="title center" style="top:18px;font-size:12.5px">Your Title <b>Slide Here</b></div>
  <div class="body" style="position:absolute;left:22px;top:40px;width:122px">Sample copy sits here to show the body style of this deck and will be swapped for real content later. Keep each line short and clear so people at the back of the room can follow the main idea. Use this block to set the scene before the four numbered points on the right, and give the audience a calm overview of what is coming next. Explain how the steps connect, which one tends to take the longest, and where most teams stumble the first time they try it. Close with a reminder that small steady changes add up over time.</div>
  <div style="position:absolute;left:153px;top:40px;width:112px;display:grid;grid-template-columns:1fr 1fr;row-gap:8px;column-gap:6px">
    <div><div class="num">01</div><div class="num-cap">Short point title<br>goes here</div><div class="num-txt">A brief line about this point for the room.</div></div>
    <div><div class="num">02</div><div class="num-cap">Short point title<br>goes here</div><div class="num-txt">A brief line about this point for the room.</div></div>
    <div><div class="num">03</div><div class="num-cap">Short point title<br>goes here</div><div class="num-txt">A brief line about this point for the room.</div></div>
    <div><div class="num">04</div><div class="num-cap">Short point title<br>goes here</div><div class="num-txt">A brief line about this point for the room.</div></div>
  </div>
  <div class="foot-logo">Ledger Lanternfox</div>
  <div class="foot-url">ledgerlanternfox.example &nbsp; 13</div>
</section>

<!-- Text + icon list -->
<section class="slide c2 r5">
  <div class="title center" style="top:18px;font-size:12.5px">Your Title <b>Slide Here</b></div>
  <div class="body" style="position:absolute;left:22px;top:40px;width:128px">Sample copy sits here to show the body style of this deck and will be swapped for real content later. Keep each line short and clear so people at the back of the room can follow the main idea. Use this block to set the scene before the list of points on the right, and give the audience a calm and friendly overview of the topic. Share why these four ideas were chosen, how they relate to daily work with data, and what a good result looks like for a busy team. End with one line that invites questions from the room.</div>
  <div style="position:absolute;left:160px;top:40px;width:104px;display:flex;flex-direction:column;gap:7px">
    <div class="icon-item"><svg viewBox="0 0 24 24" fill="none" stroke="#EB3D1F" stroke-width="2"><circle cx="12" cy="12" r="9"/><circle cx="12" cy="12" r="4"/><path d="M12 1v6M12 17v6M1 12h6M17 12h6"/></svg><div><b>Short point title goes here</b><span>A brief line about this point for the room to read.</span></div></div>
    <div class="icon-item"><svg viewBox="0 0 24 24" fill="none" stroke="#0677BA" stroke-width="2"><path d="M9 18h6M10 21h4M12 3a6 6 0 0 0-4 10.5c.7.7 1 1.5 1 2.5h6c0-1 .3-1.8 1-2.5A6 6 0 0 0 12 3Z"/></svg><div><b>Short point title goes here</b><span>A brief line about this point for the room to read.</span></div></div>
    <div class="icon-item"><svg viewBox="0 0 24 24" fill="none" stroke="#0054AA" stroke-width="2"><circle cx="12" cy="12" r="9"/><circle cx="12" cy="12" r="5"/><circle cx="12" cy="12" r="1.5"/><path d="M12 12l8-8"/></svg><div><b>Short point title goes here</b><span>A brief line about this point for the room to read.</span></div></div>
    <div class="icon-item"><svg viewBox="0 0 24 24" fill="none" stroke="#EB3D1F" stroke-width="2"><circle cx="10" cy="10" r="7"/><path d="M15 15l7 7M7 10h6M10 7v6"/></svg><div><b>Short point title goes here</b><span>A brief line about this point for the room to read.</span></div></div>
  </div>
  <div class="foot-logo">Ledger Lanternfox</div>
  <div class="foot-url">ledgerlanternfox.example &nbsp; 14</div>
</section>

<!-- Four numbered columns -->
<section class="slide c3 r5">
  <div class="title center" style="top:18px;font-size:12.5px">Your Title <b>Slide Here</b></div>
  <div style="position:absolute;left:20px;top:40px;width:242px;display:grid;grid-template-columns:repeat(4,1fr);gap:8px">
    <div><div class="num">01</div><div class="num-cap">Short point title<br>goes here</div><div class="num-txt" style="text-align:justify">Sample copy sits here to show the body style and will be swapped for real content later. Keep each line short so the back of the room can follow this step and see how it leads to the next one in the row.</div></div>
    <div><div class="num">02</div><div class="num-cap">Short point title<br>goes here</div><div class="num-txt" style="text-align:justify">Sample copy sits here to show the body style and will be swapped for real content later. Keep each line short so the back of the room can follow this step and see how it leads to the next one in the row.</div></div>
    <div><div class="num">03</div><div class="num-cap">Short point title<br>goes here</div><div class="num-txt" style="text-align:justify">Sample copy sits here to show the body style and will be swapped for real content later. Keep each line short so the back of the room can follow this step and see how it leads to the next one in the row.</div></div>
    <div><div class="num">04</div><div class="num-cap">Short point title<br>goes here</div><div class="num-txt" style="text-align:justify">Sample copy sits here to show the body style and will be swapped for real content later. Keep each line short so the back of the room can follow this step and see how it closes out the whole process.</div></div>
  </div>
  <div class="foot-logo">Ledger Lanternfox</div>
  <div class="foot-url">ledgerlanternfox.example &nbsp; 15</div>
</section>

<!-- Icon grid -->
<section class="slide c1 r6">
  <div class="title center" style="top:18px;font-size:12.5px">Your Title <b>Slide Here</b></div>
  <div style="position:absolute;left:20px;top:46px;width:242px;display:grid;grid-template-columns:repeat(3,1fr);row-gap:14px;column-gap:8px">
    <div class="icon-item"><svg viewBox="0 0 24 24" fill="none" stroke="#0677BA" stroke-width="2"><path d="M3 17a9 9 0 0 1 18 0"/><path d="M12 17l4-5"/></svg><div><b>Short point title<br>goes here</b><span>A brief line about this point, with a little more detail for the room.</span></div></div>
    <div class="icon-item"><svg viewBox="0 0 24 24" fill="none" stroke="#EB3D1F" stroke-width="2"><circle cx="12" cy="12" r="9"/><circle cx="12" cy="12" r="4"/><path d="M12 1v6M12 17v6M1 12h6M17 12h6"/></svg><div><b>Short point title<br>goes here</b><span>A brief line about this point, with a little more detail for the room.</span></div></div>
    <div class="icon-item"><svg viewBox="0 0 24 24" fill="none" stroke="#0054AA" stroke-width="2"><circle cx="12" cy="12" r="9"/><circle cx="12" cy="12" r="5"/><circle cx="12" cy="12" r="1.5"/><path d="M12 12l8-8"/></svg><div><b>Short point title<br>goes here</b><span>A brief line about this point, with a little more detail for the room.</span></div></div>
    <div class="icon-item"><svg viewBox="0 0 24 24" fill="none" stroke="#0054AA" stroke-width="2"><path d="M6 2h12M6 22h12M7 2c0 6 10 6 10 10S7 16 7 22M17 2c0 6-10 6-10 10s10 4 10 10"/></svg><div><b>Short point title<br>goes here</b><span>A brief line about this point, with a little more detail for the room.</span></div></div>
    <div class="icon-item"><svg viewBox="0 0 24 24" fill="none" stroke="#0677BA" stroke-width="2"><path d="M9 18h6M10 21h4M12 3a6 6 0 0 0-4 10.5c.7.7 1 1.5 1 2.5h6c0-1 .3-1.8 1-2.5A6 6 0 0 0 12 3Z"/></svg><div><b>Short point title<br>goes here</b><span>A brief line about this point, with a little more detail for the room.</span></div></div>
    <div class="icon-item"><svg viewBox="0 0 24 24" fill="none" stroke="#EB3D1F" stroke-width="2"><circle cx="10" cy="10" r="7"/><path d="M15 15l7 7M7 10h6M10 7v6"/></svg><div><b>Short point title<br>goes here</b><span>A brief line about this point, with a little more detail for the room.</span></div></div>
  </div>
  <div class="foot-logo">Ledger Lanternfox</div>
  <div class="foot-url">ledgerlanternfox.example &nbsp; 16</div>
</section>

<!-- Q&A -->
<section class="slide qa c2 r6">
  <svg class="fill" style="inset:0" width="280" height="157" viewBox="0 0 280 157" role="img" aria-label="Photo of a laptop keyboard along the lower edge">
    <path d="M0 157 V128 H220 L280 90 V157 Z" fill="#1b2233"/>
    <path d="M0 122 H228 L280 84 V92 L222 130 H0 Z" fill="#EB3D1F"/>
    <path d="M0 60 V122 H228 L280 84 V50 Z" fill="#0677BA" opacity=".35"/>
  </svg>
  <div class="fill" role="img" aria-label="Superhero hands revealing the brand emblem" style="left:20px;top:38px;width:90px;height:55px;border-radius:6px;background:rgba(0,60,130,.5)"></div>
  <div class="mark" style="left:20px;top:38px;width:90px;height:55px;font-size:6px;color:var(--red)">Ledger Lanternfox</div>
  <h2>Q&amp;A</h2>
  <div class="foot-url light">ledgerlanternfox.example &nbsp; 17</div>
</section>

<!-- Contact / Thanks -->
<section class="slide contact c3 r6">
  <div class="fill" role="img" aria-label="Red toned photo of a sunset over the sea" style="inset:0;background:linear-gradient(180deg,rgba(255,170,150,.25),transparent 40%,rgba(150,20,20,.25))"></div>
  <svg class="fill" style="left:0;top:27px" width="130" height="105" viewBox="0 0 130 105" aria-hidden="true"><path d="M0 0 H112 C128 30 128 75 112 105 H0 Z" fill="#0054AA"/></svg>
  <h2>Contact<br>Information</h2>
  <ul>
    <li><svg viewBox="0 0 24 24" fill="none" stroke="#fff" stroke-width="2"><path d="M4 5h16v11H9l-5 4Z"/></svg>@youraccount</li>
    <li><svg viewBox="0 0 24 24" fill="none" stroke="#fff" stroke-width="2"><rect x="3" y="5" width="18" height="14"/><path d="M3 6l9 7 9-7"/></svg>your@account.example</li>
    <li><svg viewBox="0 0 24 24" fill="none" stroke="#fff" stroke-width="2"><rect x="3" y="4" width="18" height="13"/><path d="M8 21h8M12 17v4"/></svg>ledgerlanternfox.example</li>
  </ul>
  <div class="thanks"><b>Thanks</b><span>For Your watching</span></div>
  <div class="foot-url light">ledgerlanternfox.example &nbsp; 18</div>
</section>

</main>
</body>
</html>
```